Postcard design to acquire new clients for my Property Management Company

I'm looking for a postcard design that I can send to prospective clients detailing information about my company and services.
Postcard should be eye catching and contain information from www.bramblecrestpm.com. I've provided a few screen shots for the most important information and my logo.
Target Market(s)
Real Estate
Industry/Entity Type
Real Estate
Font styles to use
Sans Serif
Requirements
Must have
- Must be eye catching!! this will be a direct mail piece - I'd like for the card to be read and not tossed in the trash immediately.
Design que from the logo.
A place to write / print the receipts name and address.
our physical address - 2387 Hollow Pine Road, Lubbock, TX 79852.
Should not have
- the contact information on the business card is not accurate - please use info from website.

```html
<!DOCTYPE html>
<html lang="en">
<head>
<meta charset="utf-8">
<title>Bramblecrest Property Management – Postcard</title>
<link rel="stylesheet" href="https://fonts.googleapis.com/css2?family=Montserrat:wght@500;600&family=Roboto:wght@400;500;700&family=Roboto+Condensed:wght@400;700&display=swap">
<style>
  :root{
    --navy:#0c3c6c;
    --blue:#1a5b96;
    --deep:#082a4e;
    --grey:#a8aaad;
    --grey-dark:#6d6f72;
    --light:#f1f1f1;
    --white:#ffffff;
    --ink:#333a42;
  }
  *{box-sizing:border-box;margin:0;padding:0}
  html,body{width:1078px;height:1200px;overflow:hidden}
  body{background:#e4e5e7;font-family:"Roboto",Arial,sans-serif;position:relative;color:var(--ink)}
  .card{position:absolute;left:128px;width:800px;height:500px;background:var(--white);overflow:hidden;box-shadow:0 4px 10px rgba(0,0,0,.25)}
  .card-front{top:85px}
  .card-back{top:625px}
  .shapes{position:absolute;inset:0}
  .abs{position:absolute}

  .brand{position:absolute;left:22px;font-family:"Montserrat",Arial,sans-serif;color:var(--navy)}
  .brand-name{font-size:31px;font-weight:600;letter-spacing:4.6px;line-height:1;white-space:nowrap}
  .brand-sub{font-size:16px;font-weight:500;letter-spacing:2.6px;margin-top:7px;white-space:nowrap}

  .headline{left:24px;top:140px;color:var(--white);font-weight:500;font-size:27px;line-height:34px;letter-spacing:.3px;white-space:nowrap}
  .tagline{left:28px;top:236px;font-size:17.5px;line-height:22px;color:#55595e}

  .services{position:absolute;left:0;top:305px;width:800px;height:155px;display:flex}
  .service{width:100px;text-align:center;color:var(--white);padding-top:12px}
  .service-icon{width:58px;height:58px;border-radius:50%;border:2px solid var(--white);background:var(--blue);margin:0 auto;display:flex;align-items:center;justify-content:center}
  .service-title{font-size:9.6px;font-weight:700;margin-top:11px;white-space:nowrap}
  .service-text{font-size:7.6px;line-height:9.5px;margin:7px 4px 0;color:#dfe8f2}

  .contact-bar{position:absolute;left:0;top:460px;width:800px;height:40px}
  .phone{font-family:"Roboto Condensed",Arial,sans-serif;font-size:27px;color:var(--navy);display:flex;align-items:center;gap:8px;white-space:nowrap}
  .contact-item{color:var(--white);font-size:16px;display:flex;align-items:center;gap:8px;white-space:nowrap}

  .pricing-tab{left:27px;top:105px;color:var(--white);font-size:22px;font-weight:500;letter-spacing:.5px}
  .plan{position:absolute;top:147px;width:138px;height:206px;background:var(--white);box-shadow:0 2px 6px rgba(0,0,0,.2)}
  .plan-featured{top:141px;height:220px}
  .plan-head{background:var(--navy);color:var(--white);font-size:13px;font-weight:500;text-align:center;height:27px;line-height:27px}
  .plan-rate{text-align:center;color:var(--navy);font-size:29px;font-weight:500;margin-top:10px;line-height:30px}
  .plan-basis{text-align:center;font-size:7px;color:#555;margin-top:1px}
  .plan-list{list-style:none;margin:16px 0 0 8px}
  .plan-list li{font-size:7.2px;line-height:13.8px;color:#444;padding-left:10px;position:relative;white-space:nowrap}
  .plan-list li::before{content:"";position:absolute;left:0;top:3px;width:5px;height:3px;border-left:1.5px solid var(--navy);border-bottom:1.5px solid var(--navy);transform:rotate(-45deg)}
  .popular{left:187px;top:130px;width:108px;height:12px;background:var(--grey);color:var(--white);font-size:6.5px;text-align:center;line-height:12px;border-radius:3px 3px 0 0}

  .cta{left:24px;top:392px;color:var(--white);font-size:15.5px;font-weight:500;letter-spacing:.4px;white-space:nowrap}
  .cta-phone{left:20px;top:428px;color:var(--white);font-family:"Roboto Condensed",Arial,sans-serif;font-size:27px;display:flex;align-items:center;gap:8px;white-space:nowrap}
  .back-link{top:473px;font-size:15px}

  .mailing{left:504px;top:58px;color:var(--navy);font-size:13px;line-height:17px;font-style:normal}
  .mailing-name{font-size:16px;font-weight:500;margin-bottom:2px}
  .stamp{left:654px;top:39px;width:126px;height:86px;border:1px solid var(--grey)}
  .address-line{position:absolute;left:496px;width:294px;height:1px;background:var(--grey)}
</style>
</head>
<body>

<section class="card card-front">
  <svg class="shapes" width="800" height="500" viewBox="0 0 800 500">
    <defs>
      <linearGradient id="bandTone" x1="0" y1="0" x2="1" y2="0">
        <stop offset="0" stop-color="#0c3c6c"/>
        <stop offset=".5" stop-color="#1a5b96"/>
        <stop offset="1" stop-color="#0c3c6c"/>
      </linearGradient>
    </defs>
    <polygon points="412,0 432,0 364,298 344,298" fill="var(--grey)"/>
    <polygon points="0,128 414,128 396,215 0,215" fill="var(--navy)"/>
    <polygon points="0,298 800,298 800,305 0,305" fill="var(--grey)"/>
    <rect x="0" y="305" width="800" height="155" fill="url(#bandTone)"/>
    <rect x="0" y="460" width="800" height="40" fill="#d9dadc"/>
    <polygon points="310,460 800,460 800,500 296,500" fill="var(--grey)"/>
    <polygon points="304,460 312,460 300,500 292,500" fill="var(--navy)"/>
  </svg>
  <div class="abs" role="img" aria-label="Photo of a person reviewing documents at a desk beside a model house"
       style="left:0;top:0;width:800px;height:298px;clip-path:polygon(434px 0,800px 0,800px 298px,366px 298px);background:linear-gradient(135deg,#c5c9d0,#eceef1 55%,#b4bac4)"></div>

  <div class="brand" style="top:58px">
    <div class="brand-name">BRAMBLECREST</div>
    <div class="brand-sub">PROPERTY MANAGEMENT</div>
  </div>

  <h1 class="abs headline">PROPERTY MANAGEMENT<br>ACROSS LUBBOCK, TX</h1>
  <p class="abs tagline">Maximize your financial returns with<br>support from our rental specialists</p>

  <div class="services">
    <div class="service">
      <div class="service-icon"><svg width="26" height="26" viewBox="0 0 24 24"><path d="M12 3 2 12h3v8h5v-5h4v5h5v-8h3z" fill="#fff"/></svg></div>
      <div class="service-title">Property Marketing</div>
      <div class="service-text">Let us take over your marketing for you and we'll find a qualified renter quickly.</div>
    </div>
    <div class="service">
      <div class="service-icon"><svg width="30" height="26" viewBox="0 0 30 24"><circle cx="10" cy="7" r="4.5" fill="#fff"/><circle cx="20" cy="7" r="4.5" fill="#fff"/><path d="M2 21c0-5 4-8 8-8s8 3 8 8zM14 21c0-5 3-8 6-8s8 3 8 8z" fill="#fff"/></svg></div>
      <div class="service-title">Tenant Screening</div>
      <div class="service-text">We screen all applications using fair housing guidelines to protect you.</div>
    </div>
    <div class="service">
      <div class="service-icon"><svg width="26" height="30" viewBox="0 0 24 28"><text x="12" y="23" text-anchor="middle" font-family="Roboto,Arial,sans-serif" font-size="26" font-weight="700" fill="#fff">$</text></svg></div>
      <div class="service-title">Rent Collection</div>
      <div class="service-text">We keep your tenants current, say hello to consistent payments.</div>
    </div>
    <div class="service">
      <div class="service-icon"><svg width="26" height="26" viewBox="0 0 24 24"><path d="M4 20 14 10" stroke="#fff" stroke-width="3" stroke-linecap="round"/><path d="M11 5l5-2 5 5-2 2-3-1-3 3-3-3 3-3z" fill="#fff"/></svg></div>
      <div class="service-title">Maintenance</div>
      <div class="service-text">Let us coordinate repair work on your behalf!</div>
    </div>
    <div class="service">
      <div class="service-icon"><svg width="26" height="26" viewBox="0 0 24 24"><circle cx="10" cy="10" r="6" fill="none" stroke="#fff" stroke-width="3"/><path d="M15 15l6 6" stroke="#fff" stroke-width="3.5" stroke-linecap="round"/></svg></div>
      <div class="service-title">Property Inspections</div>
      <div class="service-text">We visit every home in our portfolio regularly. We have proactive property management approach.</div>
    </div>
    <div class="service">
      <div class="service-icon"><svg width="26" height="26" viewBox="0 0 24 24"><path d="M3 3v18h18" fill="none" stroke="#fff" stroke-width="2"/><rect x="7" y="12" width="2.5" height="6" fill="#fff"/><rect x="11" y="8" width="2.5" height="10" fill="#fff"/><rect x="15" y="10" width="2.5" height="8" fill="#fff"/></svg></div>
      <div class="service-title">Financial Reporting</div>
      <div class="service-text">We generate monthly statements so you can review income &amp; expenses at a moment's notice.</div>
    </div>
    <div class="service">
      <div class="service-icon"><svg width="24" height="26" viewBox="0 0 24 26"><path d="M12 2 3 5v7c0 6 4 10 9 12 5-2 9-6 9-12V5z" fill="#fff"/><path d="M12 5v16c3.5-1.6 6-4.5 6-9V7z" fill="var(--blue)"/></svg></div>
      <div class="service-title">Evictions</div>
      <div class="service-text">We will handle evictions for you &amp; find new renters when its over.</div>
    </div>
    <div class="service">
      <div class="service-icon"><svg width="28" height="26" viewBox="0 0 28 24"><path d="M14 2v19M6 21h16M4 5h20" stroke="#fff" stroke-width="2"/><path d="M1 13l3-8 3 8zM21 13l3-8 3 8z" fill="none" stroke="#fff" stroke-width="1.5"/><path d="M1 13h6a3 3 0 0 1-6 0zM21 13h6a3 3 0 0 1-6 0z" fill="#fff"/></svg></div>
      <div class="service-title">Legal Guidance</div>
      <div class="service-text">Many ordinances and housing laws governing your relationship with your tenants.</div>
    </div>
  </div>

  <div class="contact-bar">
    <div class="abs phone" style="left:28px;top:4px">
      <svg width="22" height="26" viewBox="0 0 20 26"><rect x="3" y="1" width="13" height="24" rx="2.5" fill="var(--navy)"/><rect x="5.5" y="4" width="8" height="15" fill="#d9dadc"/><circle cx="9.5" cy="22" r="1.3" fill="#d9dadc"/></svg>
      (806) 555-0147
    </div>
    <div class="abs contact-item" style="left:328px;top:11px">
      <svg width="14" height="11" viewBox="0 0 14 11"><rect width="14" height="11" rx="1.5" fill="var(--navy)"/><path d="M1.5 2l5.5 4 5.5-4" fill="none" stroke="#fff" stroke-width="1.2"/></svg>
      info@bramblecrestpm.com
    </div>
    <div class="abs contact-item" style="left:556px;top:11px">
      <svg width="15" height="15" viewBox="0 0 16 16"><rect width="16" height="16" rx="2" fill="var(--navy)"/><circle cx="8" cy="8" r="5" fill="none" stroke="#fff"/><path d="M3 8h10M8 3c-3 3-3 7 0 10M8 3c3 3 3 7 0 10" fill="none" stroke="#fff" stroke-width=".8"/></svg>
      <span style="margin-left:18px">www.bramblecrestpm.com</span>
    </div>
  </div>
</section>

<section class="card card-back">
  <svg class="shapes" width="800" height="500" viewBox="0 0 800 500">
    <rect x="0" y="0" width="464" height="500" fill="var(--light)"/>
    <polygon points="0,105 156,105 170,135 0,135" fill="var(--navy)"/>
    <rect x="0" y="133" width="464" height="2" fill="var(--navy)"/>
    <rect x="0" y="378" width="464" height="122" fill="var(--navy)"/>
    <polygon points="0,422 388,422 402,465 0,465" fill="var(--grey)"/>
  </svg>

  <div class="brand" style="top:40px">
    <div class="brand-name">BRAMBLECREST</div>
    <div class="brand-sub">PROPERTY MANAGEMENT</div>
  </div>

  <h2 class="abs pricing-tab">PRICING</h2>

  <div class="abs popular">Our Most Popular</div>

  <article class="plan" style="left:23px">
    <div class="plan-head">LEASE ONLY</div>
    <div class="plan-rate">9%</div>
    <div class="plan-basis">of annual lease</div>
    <ul class="plan-list">
      <li>Professional Photography</li>
      <li>Marketing &amp; Advertising</li>
      <li>Property Showings</li>
      <li>Tenant Screening &amp; Qualifications</li>
      <li>Lease Execution</li>
      <li>Move In Coordination</li>
    </ul>
  </article>

  <article class="plan plan-featured" style="left:169px">
    <div class="plan-head">FULL SERVICE</div>
    <div class="plan-rate">10%</div>
    <div class="plan-basis">of monthly rent</div>
    <ul class="plan-list" style="margin-top:12px">
      <li>Includes Leasing Service</li>
      <li>24/7 Emergency Response</li>
      <li>Move In &amp; Out Inspections</li>
      <li>Professional Lease Enforcement</li>
      <li>Schedule &amp; Oversee all Repairs</li>
      <li>Pay all Invoices</li>
      <li>Monthly &amp; Year End Statements</li>
      <li>Annual Market Rent Analysis</li>
    </ul>
  </article>

  <article class="plan" style="left:313px">
    <div class="plan-head">PREMIUM SERVICE</div>
    <div class="plan-rate">12%</div>
    <div class="plan-basis">of monthly rent</div>
    <ul class="plan-list">
      <li>Includes Full Service Features</li>
      <li>Professional Video Marketing</li>
      <li>Home Warranty Coordination</li>
      <li>Tenant Retention Program</li>
    </ul>
  </article>

  <p class="abs cta">CHOOSE THE RIGHT PROPERTY MANAGEMENT SYSTEM</p>
  <div class="abs cta-phone">
    CONTACT US
    <svg width="20" height="24" viewBox="0 0 20 26"><rect x="3" y="1" width="13" height="24" rx="2.5" fill="#fff"/><rect x="5.5" y="4" width="8" height="15" fill="var(--grey)"/><circle cx="9.5" cy="22" r="1.3" fill="var(--grey)"/></svg>
    (806) 555-0147
  </div>
  <div class="abs contact-item back-link" style="left:25px">
    <svg width="14" height="11" viewBox="0 0 14 11"><rect width="14" height="11" rx="1.5" fill="var(--grey)"/><path d="M1.5 2l5.5 4 5.5-4" fill="none" stroke="var(--navy)" stroke-width="1.2"/></svg>
    info@bramblecrestpm.com
  </div>
  <div class="abs contact-item back-link" style="left:250px">
    <svg width="15" height="15" viewBox="0 0 16 16"><rect width="16" height="16" rx="2" fill="var(--grey)"/><circle cx="8" cy="8" r="5" fill="none" stroke="var(--navy)"/><path d="M3 8h10M8 3c-3 3-3 7 0 10M8 3c3 3 3 7 0 10" fill="none" stroke="var(--navy)" stroke-width=".8"/></svg>
    www.bramblecrestpm.com
  </div>

  <address class="abs mailing">
    <div class="mailing-name">BRAMBLECREST</div>
    2387 Hollow Pine Road,<br>Lubbock, TX 79852
  </address>
  <div class="abs stamp"></div>
  <div class="address-line" style="top:204px"></div>
  <div class="address-line" style="top:264px"></div>
  <div class="address-line" style="top:314px"></div>
</section>

</body>
</html>
```